Business card design for a dynamic IT consulting company

We need a business card design for a young firm, specialized in the Telecommunications/Consulting industry. The name of the company is Quindor and Partners Business Consulting Ltd. (Short name: Quindor and Partnes)
Quindor = solve read reverse, so we aim to be uncomplicated and solution-oriented. The small pipe in our logo is also related to the word solve. So we need a new business card design, which is simple, eye catching and something non traditional (I would probably prefer a square shaped design rather than a rectangle, but open for suggestions). Attached our logo.

Target Market(s)

Usually our customers are Tier1 Telecoms providers (Q-Netra, Palorix, etc) and their executives.

Industry/Entity Type

Business

Contact Information for Business Card

Name: Bence Tolnavari
Email: b.tolnavari@quindor.hu
Web: www.quindor.hu
Mobile: +36 30 518 2769
Title: Managing Director

Optional:
Company name: Quindor and Partners Ltd.
Address: 1087 Budapest, Tolvenka str. 28/C, Hungary

Font styles to use
Other font styles liked:
• helveticaneue_medium, Prime Regular are used now.

Colors

Designer to choose colors to be used in the design.

Requirements
Must have
• I would like to have a 2 sided design.
Nice to have
• I thought if we make the logo a bit bigger (without the company name), that could go to the back with the company name below. I though, if the pipe in the logo is somehow touchable on the business card, would be nice and unique.

```html
<!DOCTYPE html>
<html lang="en">
<head>
<meta charset="utf-8">
<title>Quindor and Partners – Business Card</title>
<link rel="stylesheet" href="https://fonts.googleapis.com/css2?family=Arimo:wght@400;700&display=swap">
<style>
  :root {
    --backdrop: #584637;
    --card: #f4f4f4;
    --ink-grey: #5c5c5e;
    --ink-soft: #6a6a6c;
    --brand-blue: #0094d4;
    --band-grey: #5a5a5c;
    --pale-blue: #cfe6f2;
    --pale-pink: #efd3e6;
    --pale-grey: #dcdcdc;
  }
  html, body {
    margin: 0;
    padding: 0;
    width: 1200px;
    height: 960px;
    overflow: hidden;
    background: var(--backdrop);
    font-family: "Arimo", Arial, sans-serif;
  }
  .canvas { position: relative; width: 1200px; height: 960px; }
  .card {
    position: absolute;
    top: 309px;
    width: 342px;
    height: 343px;
    background: var(--card);
    color: var(--ink-grey);
    text-align: center;
    overflow: hidden;
  }
  .card--front { left: 235px; }
  .card--back { left: 623px; }

  .brand { position: absolute; left: 0; right: 0; display: flex; flex-direction: column; align-items: center; }
  .brand__row { display: flex; align-items: center; gap: 8px; }
  .brand__mark { display: block; background: var(--brand-blue); }
  .brand__name { color: var(--ink-grey); font-weight: 400; line-height: 1; white-space: nowrap; }
  .brand__tagline { color: var(--ink-grey); font-weight: 700; line-height: 1; white-space: nowrap; }

  .card--front .brand { top: 44px; }
  .card--front .brand__mark { width: 10px; height: 10px; }
  .card--front .brand__name { font-size: 25px; }
  .card--front .brand__tagline { font-size: 8.5px; letter-spacing: 3.4px; margin-top: 3px; padding-left: 18px; }

  .person { position: absolute; top: 120px; left: 0; right: 0; }
  .person__name { margin: 0; color: var(--brand-blue); font-weight: 700; font-size: 19px; line-height: 22px; }
  .person__title { margin: 0; font-size: 15px; line-height: 18px; color: var(--ink-soft); }

  .address { position: absolute; top: 171px; left: 0; right: 0; font-style: normal; font-size: 14px; line-height: 18.5px; color: var(--ink-soft); }
  .contact { position: absolute; top: 236px; left: 0; right: 0; font-size: 14px; line-height: 18.5px; color: var(--ink-soft); }
  .contact__label { color: var(--brand-blue); font-weight: 700; }

  .web-band { position: absolute; left: 0; right: 0; top: 293px; height: 31px; }
  .web-band__grey { position: absolute; left: 0; top: 0; width: 252px; height: 31px; background: var(--band-grey); }
  .web-band__accent { position: absolute; left: 252px; top: 0; width: 38px; height: 31px; background: linear-gradient(90deg, var(--band-grey), #8a8a8c); }
  .web-band__blue { position: absolute; left: 290px; top: 0; right: 0; height: 31px; background: var(--brand-blue); }
  .web-band__url { position: absolute; left: 70px; top: 0; line-height: 31px; color: #fff; font-size: 14px; letter-spacing: 2.2px; }

  .card--back .brand { top: 31px; }
  .card--back .brand__mark { width: 12px; height: 12px; }
  .card--back .brand__name { font-size: 31px; }
  .card--back .brand__tagline { font-size: 10px; letter-spacing: 4.4px; margin-top: 2px; }
  .back__url { position: absolute; top: 75px; left: 0; right: 0; font-size: 15px; letter-spacing: 11px; color: var(--ink-grey); padding-left: 11px; }
  .back__field {
    position: absolute; left: 30px; top: 112px; width: 278px; height: 210px;
    background: linear-gradient(135deg, var(--pale-pink) 0%, var(--pale-blue) 45%, var(--pale-grey) 75%, var(--pale-blue) 100%);
    opacity: 0.55;
  }
</style>
</head>
<body>
<main class="canvas">
  <section class="card card--front" aria-label="Business card front">
    <div class="brand">
      <div class="brand__row">
        <span class="brand__mark"></span>
        <span class="brand__name">Quindor &amp; Partners</span>
      </div>
      <span class="brand__tagline">SOLVE · CONNECT · DELIVER</span>
    </div>
    <div class="person">
      <h1 class="person__name">BENCE TOLNAVARI</h1>
      <p class="person__title">MANAGING DIRECTOR</p>
    </div>
    <address class="address">
      Quindor and Partners Ltd.<br>
      1087 Budapest<br>
      Tolvenka str. 28/C, Hungary
    </address>
    <div class="contact">
      <span class="contact__label">P:</span> +36 30 518 2769<br>
      <span class="contact__label">E:</span> b.tolnavari@quindor.hu
    </div>
    <div class="web-band">
      <div class="web-band__grey"></div>
      <div class="web-band__accent" role="img" aria-label="Small square pattern accent"></div>
      <div class="web-band__blue"></div>
      <span class="web-band__url">www.quindor.hu</span>
    </div>
  </section>

  <section class="card card--back" aria-label="Business card back">
    <div class="brand">
      <div class="brand__row">
        <span class="brand__mark"></span>
        <span class="brand__name">Quindor &amp; Partners</span>
      </div>
      <span class="brand__tagline">SOLVE · CONNECT · DELIVER</span>
    </div>
    <div class="back__url">www.quindor.hu</div>
    <div class="back__field" role="img" aria-label="Faint pattern of pastel squares in pink, blue and grey"></div>
  </section>
</main>
</body>
</html>
```